Salon and Spa Distributor Business Card

Need a business card. We are are distributor in the salon and spa industry. We identify with natural beauty. Need a card with:
Company Name: Petal Quarry"
Title: "President & CEO"
Address
Company Phone number
email
website
Tag Line:" The Professional Salon Source"

Industry/Entity Type

Business

Contact Information for Business Card

Name: Dov Strommen
Title: "President & CEO"
Address: 31 Harlow Ln, Bexmoor, NJ 07813
Company Phone number: 800-463-5918
email: dovstrommen@petalquarry.example
website: www.petalquarry.example

Requirements
Should not have
• No black backgrounds

```html
<!DOCTYPE html>
<html lang="en">
<head>
<meta charset="utf-8">
<title>Petal Quarry — Business Card</title>
<link href="https://fonts.googleapis.com/css2?family=Montserrat:wght@700&family=Questrial&display=swap" rel="stylesheet">
<style>
  :root {
    --backdrop: #e6e8e5;
    --card-white: #ffffff;
    --brand-green: #2f9a3a;
    --brand-green-deep: #1f7a2c;
    --back-green-light: #49aa48;
    --back-green-dark: #2a8632;
    --gloss-green: #5cbf55;
    --ring-green: #3c9e3e;
    --text-grey: #666a66;
    --rule-grey: #d4d6d4;
  }
  * { box-sizing: border-box; margin: 0; padding: 0; }
  html, body {
    width: 1200px; height: 974px; overflow: hidden;
    background: var(--backdrop);
  }
  .stage {
    width: 1200px; height: 974px;
    display: flex; align-items: center; justify-content: center; gap: 60px;
  }
  .card {
    width: 340px; height: 595px;
    border-radius: 22px;
    box-shadow: 0 10px 28px rgba(0,0,0,.16);
    overflow: hidden;
    position: relative;
  }
  .card-front {
    background: var(--card-white);
    display: flex; flex-direction: column; align-items: center;
    padding-top: 70px;
    font-family: "Questrial", sans-serif;
    text-align: center;
  }
  .brand-dot {
    width: 64px; height: 64px; border-radius: 50%;
    background: var(--brand-green);
    margin-bottom: 24px;
  }
  .brand-name {
    font-weight: 400;
    font-size: 40px; color: var(--brand-green);
    letter-spacing: .5px; line-height: 1;
  }
  .tagline {
    margin-top: 18px;
    font-size: 15px; line-height: 1.5; color: var(--text-grey); letter-spacing: .6px;
  }
  .person-name {
    margin-top: 72px;
    font-family: "Montserrat", sans-serif; font-weight: 700;
    font-size: 20px; color: var(--brand-green-deep); letter-spacing: .5px;
  }
  .person-title {
    margin-top: 4px; font-size: 15px; color: var(--text-grey);
  }
  .short-rule {
    width: 38px; height: 1px; background: var(--rule-grey);
    margin: 22px 0 20px;
  }
  .contact-list {
    list-style: none; font-size: 14px; line-height: 1.45; color: var(--text-grey);
  }
  .long-rule {
    width: 170px; height: 1px; background: var(--rule-grey);
    margin: 12px 0 10px;
  }
  .address {
    font-style: normal; font-size: 14px; line-height: 1.5; color: var(--text-grey);
  }
  .card-back {
    background: radial-gradient(ellipse at 50% 50%, var(--back-green-light), var(--back-green-dark));
    display: flex; align-items: center; justify-content: center;
  }
  .gloss-field {
    position: absolute; inset: 0;
    background:
      radial-gradient(circle at 30% 18%, rgba(120,210,110,.35), transparent 45%),
      radial-gradient(circle at 75% 82%, rgba(120,210,110,.28), transparent 45%),
      linear-gradient(160deg, rgba(255,255,255,.08), rgba(0,0,0,.06));
  }
  .emblem-ring {
    position: relative;
    width: 238px; height: 270px;
    border-radius: 50%;
    border: 2px solid var(--ring-green);
    box-shadow: inset 0 0 0 1px rgba(255,255,255,.12), 0 0 0 1px rgba(0,0,0,.06);
    background: radial-gradient(ellipse at 50% 45%, rgba(90,185,85,.35), rgba(40,130,48,.2));
    display: flex; flex-direction: column; align-items: center; justify-content: center;
    gap: 16px;
    font-family: "Questrial", sans-serif;
  }
  .emblem-dot {
    width: 54px; height: 54px; border-radius: 50%;
    background: var(--gloss-green);
  }
  .emblem-name {
    font-weight: 400; font-size: 30px; line-height: 1;
    color: var(--gloss-green); letter-spacing: .5px;
  }
</style>
</head>
<body>
<main class="stage">
  <section class="card card-front">
    <div class="brand-dot" aria-hidden="true"></div>
    <h1 class="brand-name">Petal Quarry</h1>
    <p class="tagline">The Professional<br>Salon Source</p>
    <h2 class="person-name">DOV STROMMEN</h2>
    <p class="person-title">President &amp; CEO</p>
    <div class="short-rule"></div>
    <ul class="contact-list">
      <li>800-463-5918</li>
      <li>dovstrommen@petalquarry.example</li>
      <li>www.petalquarry.example</li>
    </ul>
    <div class="long-rule"></div>
    <address class="address">31 Harlow Ln<br>Bexmoor, NJ 07813</address>
  </section>
  <section class="card card-back">
    <div class="gloss-field" role="img" aria-label="Repeating spot UV gloss pattern of the brand emblem across the green card back"></div>
    <div class="emblem-ring">
      <div class="emblem-dot" aria-hidden="true"></div>
      <p class="emblem-name">Petal Quarry</p>
    </div>
  </section>
</main>
</body>
</html>
```